Meal Plan Website Needs New Pages Designed

Brightwick Supper Kits is an online, membership based program that delivers weekly meal programs (7 days worth of recipes plus shopping lists) carefully crafted by an expert team of meal planners. All recipes are created to comply with the following macronutrient ratio: 65% healthy fats, 25% lean protein, 10% good carbs.
All recipes are Paleo friendly and a great resource for those individuals who want to correctly implement this type of diet.

We are re-designing our website and need the following pages designed:

· Home page w/ logo
· How it works page
· Get Started! page
· Recipes Page template (these will be the pages on our site that will have recipes)
· Kitchen Essentials Training page (this will be a page with videos and tips + tricks, PDFs, etc)

So 5 total PSDs, 1 for each page.

Target audience: Men and women between the ages of 30 and 60 who want to:
· Eat healthy
· Lose weight
· Follow/Implement the Paleo diet
· Take the guesswork out of preparing delicious AND healthy meals for them and their families
· Know exactly what to eat, what to buy, how to make it

Feelings/Messages we want to communicate through the design:
· “Organic” but elegant look
· Fresh/light/Airy
· Simple but NOT GENERIC
· “I want to get cooking” feeling

Our Stylistic preferences:
· Minimalist with a few bold elements (something in between)
· Easy to visually navigate (enough white space, but not too much)
· There is more to “see” than to “read”

Our Color Preferences:
· Lighter pallet
· Colors that evoke natural woods, granite countertops…
· Stay away from using all dark colors

Our Font Type Preferences:
· Easy to read
· Not more than 3 font types
· Not too rigid
· Not too sophisticated
· Simple with a touch

Examples of Website Designs that we like:
· http://www.dorvanta.com/meal-plans/
· http://grulvix.com/
· https://www.mistobarn.com/

```html
<!DOCTYPE html>
<html lang="en">
<head>
<meta charset="utf-8">
<title>Brightwick Supper Kits</title>
<link href="https://fonts.googleapis.com/css2?family=Questrial&family=Open+Sans:wght@400;600&display=swap" rel="stylesheet">
<style>
  :root {
    --cream: #f1eed6;
    --cream-deep: #e6e2c2;
    --band: #ecead3;
    --peach: #f7dcbd;
    --brown: #9c6429;
    --brown-dark: #8a5620;
    --brown-text: #a3692f;
    --heading: #4e4e4e;
    --body: #4a4a4a;
    --white: #ffffff;
  }
  * { box-sizing: border-box; margin: 0; padding: 0; }
  html, body { width: 770px; height: 1200px; overflow: hidden; background: var(--white); }
  body { position: relative; font-family: "Questrial", sans-serif; color: var(--body); }
  .abs { position: absolute; }

  .site-header { position: absolute; left: 0; top: 0; width: 770px; height: 80px;
    background: radial-gradient(ellipse at 50% 40%, #f6f3df 0%, var(--cream) 55%, var(--cream-deep) 100%); }
  .brand { position: absolute; left: 84px; top: 27px; display: flex; align-items: center; gap: 8px;
    font-size: 18px; letter-spacing: 0.5px; color: var(--brown); text-transform: uppercase; }
  .brand-dot { width: 12px; height: 12px; border-radius: 50%; background: var(--brown); }
  .account { position: absolute; right: 84px; top: 20px; font-size: 10px; color: var(--brown-text); }
  .account span { margin: 0 4px; }

  .main-nav { position: absolute; left: 0; top: 74px; width: 770px; height: 36px; }
  .main-nav svg { position: absolute; left: 0; top: 0; }
  .nav-item { position: absolute; top: 16px; transform: translateX(-50%); white-space: nowrap;
    font-family: "Open Sans", sans-serif; font-size: 9.5px; color: var(--white); text-transform: uppercase; }

  .hero { position: absolute; left: 0; top: 110px; width: 770px; height: 330px; overflow: hidden; }
  .hero-photo { position: absolute; inset: 0;
    background:
      radial-gradient(ellipse 200px 90px at 390px 250px, #f3e5d2 0%, #e9d2b4 60%, transparent 100%),
      radial-gradient(ellipse 120px 60px at 260px 50px, #c9382a 0%, transparent 100%),
      linear-gradient(180deg, #b89466 0%, #a67a4e 45%, #8a5a3a 75%, #b0874e 100%); }
  .hero-title { position: absolute; left: 0; width: 770px; top: 74px; text-align: center; font-weight: 400;
    font-size: 21px; color: var(--white); letter-spacing: 0.3px; text-shadow: 0 1px 3px rgba(0,0,0,0.55); }
  .slider-arrows { position: absolute; left: 642px; top: 296px; width: 44px; height: 24px;
    background: var(--brown); border-radius: 2px; }

  .intro-title { position: absolute; left: 0; width: 770px; top: 462px; text-align: center; font-weight: 400;
    font-size: 22px; color: var(--heading); }
  .intro-text { position: absolute; left: 106px; width: 558px; top: 498px; text-align: center;
    font-size: 9.5px; line-height: 14.4px; color: var(--body); letter-spacing: 0.2px; }

  .menu-card { position: absolute; top: 563px; width: 126px; text-align: center; }
  .menu-card h3 { font-weight: 400; font-size: 16px; color: var(--heading); height: 29px; }
  .menu-photo { width: 126px; height: 93px; }
  .menu-card p { font-size: 8.2px; line-height: 11px; margin-top: 5px; color: var(--body); }
  .menu-card a { display: block; margin-top: 4px; font-size: 8.2px; color: var(--brown-text); text-decoration: none; }

  .feature-band { position: absolute; left: 0; top: 755px; width: 770px; height: 240px; background: var(--band); }
  .feature-title { position: absolute; left: 83px; top: 16px; font-weight: 400; font-size: 21px; line-height: 29px; color: var(--brown-text); }
  .feature-text { position: absolute; left: 83px; top: 91px; width: 295px; font-size: 8px; line-height: 14.4px; letter-spacing: -0.05px; color: var(--body); }
  .testimonials { position: absolute; left: 419px; top: 0; width: 266px; height: 240px; background: var(--peach); }
  .testimonials h2 { position: absolute; left: 17px; top: 18px; font-weight: 400; font-size: 22px; color: var(--brown-text); }
  .testimonials h4 { position: absolute; left: 17px; top: 63px; font-weight: 400; font-size: 15px; color: var(--brown-text); }
  .testimonials blockquote { position: absolute; left: 17px; top: 96px; width: 236px; font-size: 8px; line-height: 14.4px; color: var(--brown-text); }
  .testimonials .slider-arrows { left: 18px; top: 191px; }

  .ready-photo { position: absolute; left: 84px; top: 1020px; width: 202px; height: 111px; }
  .ready-title { position: absolute; left: 318px; top: 1019px; font-weight: 400; font-size: 21px; color: var(--heading); }
  .ready-text { position: absolute; left: 316px; top: 1055px; width: 372px; font-size: 8.2px; line-height: 14.4px; color: var(--body); }

  .site-footer { position: absolute; left: 0; top: 1157px; width: 770px; height: 43px;
    background: linear-gradient(180deg, var(--cream-deep), var(--cream)); }
  .site-footer p { position: absolute; left: 84px; top: 16px; font-size: 8.4px; color: var(--brown-text); }
</style>
</head>
<body>

<header class="site-header">
  <div class="brand"><span class="brand-dot"></span>Brightwick Supper Kits</div>
  <div class="account">Sign in <span>|</span> Join us</div>
</header>

<nav class="main-nav">
  <svg width="770" height="36" viewBox="0 0 770 36">
    <path fill="#9c6429" d="M0 4 Q5 0 10 4 T20 4 T30 4 T40 4 T50 4 T60 4 T70 4 T80 4 T90 4 T100 4 T110 4 T120 4 T130 4 T140 4 T150 4 T160 4 T170 4 T180 4 T190 4 T200 4 T210 4 T220 4 T230 4 T240 4 T250 4 T260 4 T270 4 T280 4 T290 4 T300 4 T310 4 T320 4 T330 4 T340 4 T350 4 T360 4 T370 4 T380 4 T390 4 T400 4 T410 4 T420 4 T430 4 T440 4 T450 4 T460 4 T470 4 T480 4 T490 4 T500 4 T510 4 T520 4 T530 4 T540 4 T550 4 T560 4 T570 4 T580 4 T590 4 T600 4 T610 4 T620 4 T630 4 T640 4 T650 4 T660 4 T670 4 T680 4 T690 4 T700 4 T710 4 T720 4 T730 4 T740 4 T750 4 T760 4 T770 4 L770 36 L0 36 Z"/>
  </svg>
  <span class="nav-item" style="left:151px">Home</span>
  <span class="nav-item" style="left:212px">About</span>
  <span class="nav-item" style="left:290px">Meal Plans</span>
  <span class="nav-item" style="left:366px">Recipes</span>
  <span class="nav-item" style="left:453px">Success Stories</span>
  <span class="nav-item" style="left:549px">Resources</span>
  <span class="nav-item" style="left:618px">Blog</span>
</nav>

<section class="hero">
  <div class="hero-photo" role="img" aria-label="Plate of spaghetti with tomatoes and basil on a wooden table beside olive oil and wine"></div>
  <h1 class="hero-title">All recipes are created to comply with the following macronutrient ratio</h1>
  <svg class="abs" style="left:0;top:0" width="770" height="330" viewBox="0 0 770 330" font-family="Questrial, sans-serif">
    <path d="M384 178 L300 178 A84 84 0 1 1 433.4 246 Z" fill="#c79358" stroke="#e2bb88" stroke-width="1.5"/>
    <path d="M384 182 L384 266 A84 84 0 0 1 300 182 Z" fill="#b9834a" stroke="#e2bb88" stroke-width="1.5"/>
    <path d="M388 182 L437.4 250 A84 84 0 0 1 388 266 Z" fill="#c18b50" stroke="#e2bb88" stroke-width="1.5"/>
    <text x="384" y="133" text-anchor="middle" font-size="15" fill="#f6e6cc">65%</text>
    <text x="384" y="150" text-anchor="middle" font-size="10" fill="#f6e6cc">Healthy Fats</text>
    <text x="353" y="208" text-anchor="middle" font-size="15" fill="#f6e6cc">25%</text>
    <text x="348" y="222" text-anchor="middle" font-size="8" fill="#f6e6cc" transform="rotate(15 348 222)">Lean Protein</text>
    <text x="412" y="218" text-anchor="middle" font-size="14" fill="#f6e6cc">10%</text>
    <text x="418" y="233" text-anchor="middle" font-size="7" fill="#f6e6cc" transform="rotate(-25 418 233)">Good Carbs</text>
  </svg>
  <div class="slider-arrows">
    <svg width="44" height="24" viewBox="0 0 44 24"><path d="M14 9 L11 12 L14 15 M30 9 L33 12 L30 15" stroke="#fff" stroke-width="1.5" fill="none"/></svg>
  </div>
</section>

<h2 class="intro-title">Genuine raw materials and ingredients!</h2>
<p class="intro-text">Proin gravida nibh vel velit auctor aliquet. Aenean sollicitudin, lorem quis bibendum auctor, nisi elit consequat ipsum, nec sagittis sem nibh id elit. Duis sed odio sit amet nibh vulputate cursus a sit amet mauris. Morbi accumsan ipsum velit. Nam nec tellus a odio tincidunt auctor a ornare odio. Sed non mauris vitae erat consequat auctor eu in elit. Class aptent taciti</p>

<article class="menu-card" style="left:83px">
  <h3>Basic Menu</h3>
  <div class="menu-photo" role="img" aria-label="Grilled meat with greens and red peppers" style="background:linear-gradient(135deg,#7a9a3a,#b5572a 50%,#e0a266)"></div>
  <p>Version of Lorem Ipsum, Proin gravida nibh vel velit auctor</p>
  <a href="#">More Info</a>
</article>
<article class="menu-card" style="left:242px">
  <h3>Vegan Menu</h3>
  <div class="menu-photo" role="img" aria-label="Vegetable noodle bowl" style="background:linear-gradient(135deg,#d9c69a,#f1e3c0 50%,#c9a76a)"></div>
  <p>Version of Lorem Ipsum, Proin gravida nibh vel velit auctor</p>
  <a href="#">More Info</a>
</article>
<article class="menu-card" style="left:400px">
  <h3>Cocktails</h3>
  <div class="menu-photo" role="img" aria-label="Blue cocktail with orange and pineapple slices" style="background:linear-gradient(135deg,#f3b62a,#f8f4e6 50%,#7ec3e0)"></div>
  <p>Version of Lorem Ipsum, Proin gravida nibh vel velit auctor</p>
  <a href="#">More Info</a>
</article>
<article class="menu-card" style="left:560px">
  <h3>Best Desserts</h3>
  <div class="menu-photo" role="img" aria-label="Chocolate souffles with pears" style="background:linear-gradient(135deg,#a3ad6a,#eee9de 50%,#6a4330)"></div>
  <p>Version of Lorem Ipsum, Proin gravida nibh vel velit auctor</p>
  <a href="#">More Info</a>
</article>

<section class="feature-band">
  <h2 class="feature-title">The Best Food to<br>Make You Feel Good!</h2>
  <p class="feature-text">This is Draftmill's version of Lorem Ipsum. Proin gravida nibh vel velit auctor aliquet. Aenean sollicitudin, lorem quis bibendum auctor, nisi elit consequat ipsum, nec sagittis sem nibh id elit. Duis sed odio sit amet nibh vulputate cursus a sit amet mauris. Morbi accumsan ipsum velit. Nam nec tellus a odio tincidunt auctor a ornare odio. Sed non mauris vitae erat consequat auctor eu in elit. Class aptent taciti sociosqu ad litora torquent per conubia nostra, per inceptos himenaeos. Mauris in erat justo. Nullam ac urna eu felis dapibus condimentum sit amet a augue. Sed non neque elit. Sed ut imperdiet nisi. Proin condimentum fermentum</p>
  <aside class="testimonials">
    <h2>Testimonials</h2>
    <h4>Client Name</h4>
    <blockquote>"Lorem Ipsum, Proin gravida nibh vel velit auctor aliquet. Aenean sollicitudin, lorem quis bibendum auctor, nisi elit consequat ipsum, nec sagittis sem nibh id elit. Duis sed odio sit amet nibh vulputate cursus a sit amet mauris. Morbi accumsan ipsum velit, Nam nec tellus a odio"</blockquote>
    <div class="slider-arrows">
      <svg width="44" height="24" viewBox="0 0 44 24"><path d="M14 9 L11 12 L14 15 M30 9 L33 12 L30 15" stroke="#fff" stroke-width="1.5" fill="none"/></svg>
    </div>
  </aside>
</section>

<div class="ready-photo" role="img" aria-label="Salad with peppers, olives, ham and croutons" style="background:linear-gradient(135deg,#d8442c,#e9c47a 40%,#3a3230 60%,#d9a05c)"></div>
<h2 class="ready-title">Always Ready to Get Healthy Meal</h2>
<p class="ready-text">Aenean sollicitudin, lorem quis bibendum auctor, nisi elit consequat ipsum, nec sagittis sem nibh id elit. Duis sed odio sit amet nibh vulputate cursus a sit amet mauris. Morbi accumsan ipsum velit. Nam nec tellus a odio tincidunt auctor a ornare odio. Sed non mauris vitae erat consequat auctor eu in elit. Class aptent taciti sociosqu ad litora torquent per conubia nostra, per inceptos himenaeos. Mauris in erat justo. Nullam ac urna eu felis</p>

<footer class="site-footer">
  <p>© Brightwick Supper Kits. All rights reserved.</p>
</footer>

</body>
</html>
```